Modern business card design for professional copywriter

I'd like a business card design that I can use to have my cards printed out by quillprint.com as a squared corners business card (see artwork and design guidelines here: https://help.quillprint.com/hc/en-gb/sections/200570950-QUILL-Product-Templates)

The design should be clean and modern and reflect the colours, tone and branding on my website: https://tessavorrin.com.au

Target Market(s)

Professionals, B2B small business owners

Industry/Entity Type

Business

Contact Information for Business Card

Tessa Vorrin
m: 0468 905 327
e: tessa@tessavorrin.com.au
w: tessavorrin.com.au

Font styles to use
Sans Serif

Requirements
Must have
• Tagline: "Smart copywriting for clever business people"
• Brand colours: fd8000, 009984, 666666 and black
Nice to have

```html
<!DOCTYPE html>
<html lang="en">
<head>
<meta charset="utf-8">
<title>Tessa Vorrin – Business Card</title>
<link rel="stylesheet" href="https://fonts.googleapis.com/css2?family=Open+Sans:wght@400;600;700&display=swap">
<style>
  :root {
    --brand-orange: #f58220;
    --brand-teal: #009984;
    --brand-grey: #666666;
    --ink: #222222;
    --card-white: #ffffff;
    --backdrop: #e6e6e6;
    --card-w: 500px;
    --card-h: 286px;
  }
  * { box-sizing: border-box; margin: 0; padding: 0; }
  html, body {
    width: 1200px;
    height: 900px;
    overflow: hidden;
    background: var(--backdrop);
    font-family: "Open Sans", Arial, sans-serif;
  }
  .stage {
    width: 1200px;
    height: 900px;
    display: flex;
    align-items: center;
    justify-content: center;
    gap: 60px;
  }
  .card {
    position: relative;
    width: var(--card-w);
    height: var(--card-h);
    overflow: hidden;
    box-shadow: 0 2px 10px rgba(0,0,0,0.12);
  }

  /* Front */
  .card--front { background: var(--card-white); }
  .card__name {
    position: absolute;
    left: 34px;
    top: 30px;
    font-size: 17px;
    font-weight: 600;
    letter-spacing: 0.04em;
    text-transform: uppercase;
  }
  .card__name-first { color: var(--brand-teal); }
  .card__name-last { color: var(--brand-orange); }

  .contact-list {
    position: absolute;
    left: 34px;
    top: 84px;
    list-style: none;
    font-size: 12px;
    color: var(--ink);
  }
  .contact-list li {
    display: flex;
    align-items: center;
    gap: 9px;
    line-height: 21px;
  }
  .contact-list svg { width: 11px; height: 11px; flex: none; }

  .brand-mark {
    position: absolute;
    right: 40px;
    top: 104px;
    display: flex;
    align-items: center;
    gap: 10px;
  }
  .brand-mark__dot {
    width: 16px;
    height: 16px;
    border-radius: 50%;
    background: var(--brand-orange);
  }
  .brand-mark__name {
    font-size: 34px;
    font-weight: 600;
    color: var(--brand-teal);
    letter-spacing: -0.01em;
  }

  .tagline-band {
    position: absolute;
    left: 0;
    right: 0;
    bottom: 0;
    height: 72px;
    background: var(--brand-orange);
    display: flex;
    align-items: center;
    padding-left: 34px;
  }
  .tagline {
    color: var(--card-white);
    font-size: 13px;
    font-weight: 600;
    letter-spacing: 0.03em;
    text-transform: uppercase;
  }

  /* Back */
  .card--back {
    background: var(--brand-orange);
    display: flex;
    align-items: center;
    justify-content: center;
  }
  .card--back .brand-mark { position: static; }
  .card--back .brand-mark__dot { background: var(--card-white); width: 18px; height: 18px; }
  .card--back .brand-mark__name { color: var(--card-white); font-size: 40px; }
</style>
</head>
<body>
  <main class="stage">
    <section class="card card--front" aria-label="Business card front">
      <h1 class="card__name"><span class="card__name-first">Tessa</span> <span class="card__name-last">Vorrin</span></h1>

      <ul class="contact-list">
        <li>
          <svg viewBox="0 0 12 12" aria-hidden="true"><rect x="3" y="0.5" width="6" height="11" rx="1.2" fill="none" stroke="var(--brand-teal)" stroke-width="1.2"/><circle cx="6" cy="9.5" r="0.7" fill="var(--brand-teal)"/></svg>
          <span>0468 905 327</span>
        </li>
        <li>
          <svg viewBox="0 0 12 12" aria-hidden="true"><rect x="0.5" y="2" width="11" height="8" rx="1" fill="var(--brand-teal)"/><path d="M1 2.8 L6 6.6 L11 2.8" fill="none" stroke="#fff" stroke-width="1"/></svg>
          <span>tessa@tessavorrin.com.au</span>
        </li>
        <li>
          <svg viewBox="0 0 12 12" aria-hidden="true"><circle cx="6" cy="6" r="5.3" fill="var(--brand-teal)"/><path d="M0.8 6 H11.2 M6 0.8 C3.5 3.5 3.5 8.5 6 11.2 M6 0.8 C8.5 3.5 8.5 8.5 6 11.2" fill="none" stroke="#fff" stroke-width="0.8"/></svg>
          <span>tessavorrin.com.au</span>
        </li>
      </ul>

      <div class="brand-mark">
        <span class="brand-mark__dot" aria-hidden="true"></span>
        <span class="brand-mark__name">Tessa Vorrin</span>
      </div>

      <div class="tagline-band">
        <p class="tagline">Smart copywriting for clever business people</p>
      </div>
    </section>

    <section class="card card--back" aria-label="Business card back">
      <div class="brand-mark">
        <span class="brand-mark__dot" aria-hidden="true"></span>
        <span class="brand-mark__name">Tessa Vorrin</span>
      </div>
    </section>
  </main>
</body>
</html>
```